Sustainably Transforming Education

Company is education services based. early learning through adult and corporate. Focus is national government policy and program design and delivery alongside a research based and academically grounded set of approaches to planning, evaluation, and change management.I am looking for an innovative design position that aligns with the global agendas for innovation, creativity and collaboration at international and national policy levels (berulo is a name that reflects these qualities - colours need to reflect amythyst in some way). I also need a design that translates from a business card as 1 medium of interaction to a template that can work in word/powerpoint etc to support both stationery as well as a digital strategy across multiple channels (fb/twit/etc)There is no slogan/tag line for the company and their is no logo. I was looking to just leverage the name - have currently played around with various fonts (ending up with cuisine - all lowercase).

Industry/Entity Type

Adult

Contact Information for Business Card

name: berulo (all lowercase)Chairman: Andrew CrowMobile: +61 418 902 131Web: www.berulo.comemail: martin.pelly@berulo-example.com

Font styles to use
Script
Other font styles liked:
• cuisine

Colors
e34298
e667a6
33a6d7
aaaaaa

Requirements
Nice to have
• https://files.example-share.net/sh/qx7kw2hd91lzmnp/AAFr3tYbQeLp8VwZnKcDs2Hu?dl=0
• Link to the printwell templates used to begin this process....the one with the lines was about people intersecting (collaborating).....the organic shapes one more of a fluid feel of people coming together - the overall shape being largely spherical could represent a "global" feel.....anyway that is how I was thinking about these

```html
<!DOCTYPE html>
<html lang="en">
<head>
<meta charset="utf-8">
<title>berulo — business card</title>
<link rel="stylesheet" href="https://fonts.googleapis.com/css2?family=Dancing+Script:wght@400;500&display=swap">
<style>
  :root {
    --backdrop: #ebebeb;
    --stripe-pink: #e667a6;
    --stripe-magenta: #e34298;
    --stripe-blue: #33a6d7;
    --stripe-amethyst: #a99bd0;
    --stripe-grey: #d6d6d6;
    --band: #333333;
    --ink-light: #ffffff;
    --accent: #e34298;
  }
  html, body {
    margin: 0;
    padding: 0;
    width: 1200px;
    height: 1152px;
    overflow: hidden;
    background: var(--backdrop);
  }
  .sheet {
    width: 1200px;
    height: 1152px;
    display: flex;
    flex-direction: column;
    align-items: center;
    justify-content: center;
    gap: 64px;
  }
  .card {
    width: 840px;
    height: 480px;
    display: block;
    box-shadow: 0 6px 18px rgba(0, 0, 0, 0.18);
  }
  .stripe-pink { fill: var(--stripe-pink); }
  .stripe-magenta { fill: var(--stripe-magenta); }
  .stripe-blue { fill: var(--stripe-blue); }
  .stripe-amethyst { fill: var(--stripe-amethyst); }
  .stripe-grey { fill: var(--stripe-grey); }
  .band { fill: var(--band); }
  .script { font-family: "Dancing Script", cursive; font-weight: 400; }
  .holder-name { fill: var(--ink-light); font-size: 64px; }
  .holder-title { fill: var(--accent); font-size: 26px; font-weight: 500; }
  .contact-line { fill: var(--ink-light); font-size: 21px; }
  .brand-name { fill: var(--ink-light); font-size: 104px; }
</style>
</head>
<body>
<main class="sheet">

  <!-- Front: name and contact details -->
  <svg class="card card-front" viewBox="0 0 840 480" xmlns="http://www.w3.org/2000/svg">
    <defs>
      <pattern id="stripes-front" patternUnits="userSpaceOnUse" width="20" height="240" patternTransform="rotate(25)">
        <rect class="stripe-pink" x="0" y="0" width="20" height="48"/>
        <rect class="stripe-magenta" x="0" y="48" width="20" height="48"/>
        <rect class="stripe-blue" x="0" y="96" width="20" height="48"/>
        <rect class="stripe-amethyst" x="0" y="144" width="20" height="48"/>
        <rect class="stripe-grey" x="0" y="192" width="20" height="48"/>
      </pattern>
      <clipPath id="clip-front"><rect width="840" height="480"/></clipPath>
    </defs>
    <g clip-path="url(#clip-front)">
      <rect width="840" height="480" fill="url(#stripes-front)"/>

      <g class="name-band" transform="translate(370 240) rotate(-65)">
        <rect class="band" x="-400" y="-76" width="800" height="152"/>
        <text class="script holder-name" x="-20" y="10" text-anchor="middle">Martin Pelly</text>
        <text class="script holder-title" x="120" y="50" text-anchor="middle">Chairman</text>
      </g>

      <g class="contact-band" transform="translate(690 240) rotate(-65)">
        <rect class="band" x="-400" y="-68" width="800" height="136"/>
        <text class="script contact-line" x="30" y="-26" text-anchor="middle">+61 427 315 086</text>
        <text class="script contact-line" x="30" y="6" text-anchor="middle">martin.pelly@berulo-example.com</text>
        <text class="script contact-line" x="30" y="38" text-anchor="middle">www.berulo-example.com</text>
      </g>
    </g>
  </svg>

  <!-- Back: brand name -->
  <svg class="card card-back" viewBox="0 0 840 480" xmlns="http://www.w3.org/2000/svg">
    <defs>
      <pattern id="stripes-back" patternUnits="userSpaceOnUse" width="20" height="240" patternTransform="rotate(25)">
        <rect class="stripe-pink" x="0" y="0" width="20" height="48"/>
        <rect class="stripe-magenta" x="0" y="48" width="20" height="48"/>
        <rect class="stripe-blue" x="0" y="96" width="20" height="48"/>
        <rect class="stripe-amethyst" x="0" y="144" width="20" height="48"/>
        <rect class="stripe-grey" x="0" y="192" width="20" height="48"/>
      </pattern>
      <clipPath id="clip-back"><rect width="840" height="480"/></clipPath>
    </defs>
    <g clip-path="url(#clip-back)">
      <rect width="840" height="480" fill="url(#stripes-back)"/>
      <g class="brand-band" transform="translate(700 240) rotate(-65)">
        <rect class="band" x="-400" y="-78" width="800" height="156"/>
        <text class="script brand-name" x="-10" y="30" text-anchor="middle">berulo</text>
      </g>
    </g>
  </svg>

</main>
</body>
</html>
```